Business Card Design

I need business cards designed for a new company i have started that makes cakes, particularly themed kids cakes with a really modern design and I would like to have my business cards reflect this. I have attached some photos of cakes I have made and would like some to be used.

Industry/Entity Type

Business

Contact Information for Business Card

Business Name: Tarts and Treats by Maren
Mobile: 0492 815 063
email: maren@tartsandtreatsbymaren.example.au
Instagram: instagram.com/tartsandtreatsbymaren/
Facebook: fb.me/tartsandtreatsbymaren

Colors
e667a6
b768aa
3276b5

Requirements
Must have
• Business Name: Tarts and Treats by Maren
• Mobile: 0492 815 063
• email: maren@tartsandtreatsbymaren.example.au
• Instagram: instagram.com/tartsandtreatsbymaren/
• Facebook: fb.me/tartsandtreatsbymaren
Nice to have
• 2 to 3 pictures of my cakes

```html
<!DOCTYPE html>
<html lang="en">
<head>
<meta charset="utf-8">
<title>Tarts and Treats by Maren — Business Cards</title>
<link rel="stylesheet" href="https://fonts.googleapis.com/css2?family=Open+Sans:wght@400;600;700&display=swap">
<style>
  :root {
    --backdrop: #ece8ea;
    --pink: #e667a6;
    --pink-deep: #d9549a;
    --orchid: #b768aa;
    --orchid-deep: #8f4d8a;
    --white: #ffffff;
    --ink: #555555;
    --shadow: rgba(70, 30, 60, 0.18);
  }
  * { box-sizing: border-box; margin: 0; padding: 0; }
  html, body {
    width: 1200px; height: 843px; overflow: hidden;
    background: var(--backdrop);
    font-family: "Open Sans", sans-serif;
  }
  .canvas { position: relative; width: 1200px; height: 843px; }

  .card {
    position: absolute; width: 600px; height: 343px;
    border-radius: 4px; overflow: hidden;
    box-shadow: 0 10px 28px var(--shadow);
  }

  /* Back of card */
  .card-back {
    left: 60px; top: 70px;
    background: linear-gradient(135deg, var(--orchid) 0%, #a85c9f 55%, var(--orchid-deep) 100%);
    display: flex; align-items: center; justify-content: center;
  }
  .card-back .brand-name {
    color: var(--white); font-weight: 600; font-size: 30px; letter-spacing: 0.5px;
    text-align: center; line-height: 1.25;
  }

  /* Front of card */
  .card-front { left: 540px; top: 430px; background: var(--white); }
  .card-front .wave { position: absolute; inset: 0; width: 600px; height: 343px; }
  .person { position: absolute; left: 76px; top: 34px; color: var(--white); }
  .person-name { font-weight: 700; font-size: 17px; letter-spacing: 0.5px; }
  .person-role { font-size: 13px; margin-top: 2px; }

  .contact-list { position: absolute; left: 20px; top: 210px; list-style: none; }
  .contact-item {
    display: flex; align-items: center; gap: 10px;
    font-size: 14px; color: var(--ink); height: 21px;
  }
  .contact-icon { width: 14px; height: 14px; flex: none; display: block; }

  .front-brand {
    position: absolute; right: 30px; bottom: 46px; width: 200px;
    color: var(--orchid); font-weight: 600; font-size: 22px; line-height: 1.2;
    text-align: center;
  }
</style>
</head>
<body>
<main class="canvas">

  <section class="card card-back" aria-label="Card back">
    <p class="brand-name">Tarts and Treats<br>by Maren</p>
  </section>

  <section class="card card-front" aria-label="Card front">
    <svg class="wave" viewBox="0 0 600 343" aria-hidden="true">
      <defs>
        <linearGradient id="band" x1="0" y1="0" x2="1" y2="0">
          <stop offset="0" stop-color="var(--pink)"/>
          <stop offset="1" stop-color="var(--pink-deep)"/>
        </linearGradient>
      </defs>
      <path d="M0 0 H600 V195 C470 112 220 122 0 140 Z" fill="url(#band)"/>
      <path d="M0 128 C210 110 450 100 600 168" fill="none" stroke="var(--orchid)" stroke-width="5"/>
      <path d="M0 140 C220 122 470 112 600 195" fill="none" stroke="var(--white)" stroke-width="3"/>
    </svg>

    <div class="person">
      <p class="person-name">ADA BROOK</p>
      <p class="person-role">CEO/Founder</p>
    </div>

    <ul class="contact-list">
      <li class="contact-item">
        <svg class="contact-icon" viewBox="0 0 14 14" aria-label="Mobile"><rect width="14" height="14" fill="var(--pink)"/><rect x="4.5" y="2.5" width="5" height="9" rx="1" fill="none" stroke="var(--white)" stroke-width="1.2"/></svg>
        0492 815 063
      </li>
      <li class="contact-item">
        <svg class="contact-icon" viewBox="0 0 14 14" aria-label="Email"><rect width="14" height="14" fill="var(--pink)"/><rect x="2.5" y="4" width="9" height="6" fill="none" stroke="var(--white)" stroke-width="1.1"/><path d="M2.5 4 L7 7.5 L11.5 4" fill="none" stroke="var(--white)" stroke-width="1.1"/></svg>
        maren@tartsandtreatsbymaren.example.au
      </li>
      <li class="contact-item">
        <svg class="contact-icon" viewBox="0 0 14 14" aria-label="Instagram"><rect width="14" height="14" fill="var(--pink)"/></svg>
        tartsandtreatsbymaren
      </li>
      <li class="contact-item">
        <svg class="contact-icon" viewBox="0 0 14 14" aria-label="Facebook"><rect width="14" height="14" fill="var(--pink)"/></svg>
        tartsandtreatsbymaren
      </li>
    </ul>

    <p class="front-brand">Tarts and Treats by Maren</p>
  </section>

</main>
</body>
</html>
```